Vale Crest - Business Cards

We are a consultancy to help builders to optimize their planning in order to save building costs. For that reason we need a clean and professional business card for our high-priced services. A QR code should lead to the contact information needed.

```html
<!DOCTYPE html>
<html lang="en">
<head>
<meta charset="utf-8">
<title>Vale Crest – Business Cards</title>
<link href="https://fonts.googleapis.com/css2?family=Play:wght@400;700&display=swap" rel="stylesheet">
<style>
  :root {
    --backdrop: #5b5b5d;
    --paper: #ffffff;
    --ink: #2c2c30;
    --gold: #c68e3a;
    --charcoal: #323238;
    --card-black: #111112;
  }
  * { box-sizing: border-box; margin: 0; padding: 0; }
  html, body {
    width: 1093px; height: 1200px; overflow: hidden;
    background: var(--backdrop);
    font-family: "Play", sans-serif;
  }
  .card {
    position: absolute;
    border-radius: 28px;
    overflow: hidden;
  }
  .card-front {
    left: 265px; top: 226px; width: 577px; height: 357px;
    background: var(--paper);
    color: var(--ink);
  }
  .holder { position: absolute; left: 37px; top: 66px; }
  .holder-name { font-size: 21px; font-weight: 700; letter-spacing: 0.3px; line-height: 1; }
  .holder-name .first { color: var(--gold); }
  .holder-role { font-size: 16px; margin-top: 4px; }
  .brand {
    position: absolute; left: 281px; top: 124px; width: 264px;
    display: flex; align-items: center; justify-content: center; gap: 10px;
  }
  .brand-mark { width: 16px; height: 16px; background: var(--gold); }
  .brand-name { font-size: 36px; font-weight: 700; color: var(--charcoal); letter-spacing: 1px; line-height: 1; }
  .contact { position: absolute; left: 37px; top: 265px; list-style: none; }
  .contact li { display: flex; align-items: center; gap: 8px; font-size: 17px; height: 21px; }
  .contact svg { width: 15px; height: 15px; flex: none; }
  .address {
    position: absolute; right: 32px; top: 286px;
    text-align: right; font-size: 17px; line-height: 21px;
  }
  .bar { position: absolute; left: 0; bottom: 0; height: 16px; }
  .bar-gold { width: 290px; background: var(--gold); }
  .bar-dark { left: 290px; right: 0; background: var(--charcoal); }
  .card-back {
    left: 265px; top: 620px; width: 583px; height: 360px;
    background: var(--card-black);
  }
</style>
</head>
<body>
  <section class="card card-front">
    <div class="holder">
      <p class="holder-name"><span class="first">DANIEL</span> HARTMANN</p>
      <p class="holder-role">Managing Director</p>
    </div>

    <div class="brand">
      <span class="brand-mark"></span>
      <span class="brand-name">Vale Crest</span>
    </div>

    <ul class="contact">
      <li>
        <svg viewBox="0 0 16 16" aria-hidden="true"><path d="M4 1.5l2.5 3-1.6 1.6c.8 1.9 2.3 3.4 4.2 4.2l1.6-1.6 3 2.5-1.7 2.4C7 13.2 2.8 9 2.2 3.2z" fill="none" stroke="var(--gold)" stroke-width="1.5" stroke-linejoin="round"/></svg>
        044-987 654 321
      </li>
      <li>
        <svg viewBox="0 0 16 16" aria-hidden="true"><rect x="1" y="3.5" width="14" height="9" fill="var(--gold)"/><path d="M1 3.5l7 5 7-5" fill="none" stroke="#fff" stroke-width="1.2"/></svg>
        hello@valecrest.com
      </li>
      <li>
        <svg viewBox="0 0 16 16" aria-hidden="true"><circle cx="8" cy="8" r="6.5" fill="none" stroke="var(--gold)" stroke-width="1.3"/><ellipse cx="8" cy="8" rx="2.8" ry="6.5" fill="none" stroke="var(--gold)" stroke-width="1.1"/><path d="M1.5 8h13M2.5 5h11M2.5 11h11" stroke="var(--gold)" stroke-width="1"/></svg>
        www.valecrest.com
      </li>
    </ul>

    <p class="address">18 Harbour Lane<br>Northland, 20418</p>

    <div class="bar bar-gold"></div>
    <div class="bar bar-dark"></div>
  </section>

  <section class="card card-back" role="img" aria-label="Card reverse: repeating grid of the company mark embossed on black, one mark highlighted in gold and silver"></section>
</body>
</html>
```